Summit Builders Web Site / Business Cards

Construction Company that specializes in Water and Fire Damage, Residential ReModels, Landscaping and Building ADU (Accessory Dwelling Unit)

Growing and changing families often need additional space, and a remodeling project can often provide that. Adding a new area, or repurposing an existing one can satisfy this requirement.

Other times, homeowners want to update the look in their kitchen or bathroom with more than just a change of cabinetry or vanity doors and drawers. Whatever your needs are, Summit Builders has skilled workers who are bonded and insured, and ready to make your dreams and visions a reality.

Target Market(s)

Home Owners

Industry/Entity Type

Construction Company

Contact Information for Business Card

Center Logo with our information on the corners

Back side to be Logo Only
Contact Info
CSLB License # 2418596
info@summitbuildersca.example
www.summitbuildersca.example

Coding

Coded - Design and coding required

Number of Pages Required

5+ page

Font styles to use
Serif
Sans Serif

Requirements
Must have
• Using our Logo Colors
Home
About Us
Services
Projects / Portfolio
Contact Us
Nice to have
• Colors matching our Logo
Should not have
• Black because it doesnt match our logo

```html
<!DOCTYPE html>
<html lang="en">
<head>
<meta charset="utf-8">
<title>Summit Builders</title>
<link href="https://fonts.googleapis.com/css2?family=Bebas+Neue&family=Montserrat:wght@400;500;600;700&family=Lato:ital,wght@0,400;0,700;1,400&display=swap" rel="stylesheet">
<style>
:root{
  --orange:#f26a1b;
  --orange-deep:#e05a10;
  --ink:#222428;
  --text:#555;
  --muted:#999;
  --line:#e6e6e6;
  --panel:#f4f4f4;
  --footer:#2b2b2d;
  --footer-deep:#232325;
  --white:#fff;
}
*{margin:0;padding:0;box-sizing:border-box}
html,body{width:1200px;height:4038px;overflow:hidden}
body{position:relative;background:var(--white);font-family:'Lato',sans-serif;color:var(--text)}
.abs{position:absolute}
.photo{position:absolute}

/* header */
.brand{left:161px;top:30px;width:100px;text-align:center;font-family:'Montserrat',sans-serif;color:var(--ink)}
.brand-mark{width:26px;height:26px;background:var(--orange);margin:0 auto 6px}
.brand-name{font-size:15px;font-weight:700;letter-spacing:1px;line-height:1.1}
.nav{left:415px;top:53px;display:flex;gap:0;font-family:'Montserrat',sans-serif;font-size:10.5px;color:#444}
.nav a{color:inherit;text-decoration:none;position:absolute;white-space:nowrap}
.nav a.active{color:var(--orange)}
.search{left:853px;top:51px}
.btn{background:var(--orange);color:var(--white);font-family:'Montserrat',sans-serif;text-align:center;clip-path:polygon(8% 0,92% 0,100% 50%,92% 100%,8% 100%,0 50%)}
.quote-btn{left:896px;top:42px;width:141px;height:36px;line-height:36px;font-size:11.5px}

/* hero */
.hero{left:0;top:0;width:1200px;height:700px;background:linear-gradient(180deg,#8c9096 0%,#a9a9a6 25%,#9a7a5a 55%,#6d4a34 80%,#b9a58a 100%)}
.hero-cut{left:0;top:0}
.hero-title{left:0;top:225px;width:1200px;text-align:center;font-family:'Bebas Neue',sans-serif;font-size:66px;line-height:68px;color:var(--white);text-shadow:0 0 3px #222,2px 2px 0 #222}
.hero-title .hl{color:var(--orange)}
.badge{left:526px;top:564px;width:148px;height:148px;border-radius:50%;background:var(--white);border:7px solid #e9e2dc;display:flex;align-items:center;justify-content:center;text-align:center;font-family:'Montserrat',sans-serif;font-weight:700;font-size:15px;color:var(--orange);line-height:1.2}

/* section heads */
.sec-head{left:0;width:1200px;text-align:center;font-family:'Montserrat',sans-serif;font-weight:700;font-size:30px;color:var(--ink)}
.sec-head span{position:relative;padding:0 28px;background:var(--white)}
.rule{height:1px;background:var(--line)}

.who-sub{left:0;top:832px;width:1200px;text-align:center;font-family:'Montserrat',sans-serif;font-size:14px;color:var(--orange)}
.who-text{left:365px;top:860px;width:470px;text-align:center;font-size:10.5px;line-height:20px;color:#888}

.feat-bg{background:var(--panel)}
.feat{background:var(--white);box-shadow:0 1px 6px rgba(0,0,0,.08);padding:22px 24px}
.feat h4{font-family:'Montserrat',sans-serif;font-weight:500;font-size:11.5px;color:var(--ink);line-height:16px;text-transform:uppercase}
.feat p{font-size:10px;line-height:19px;color:var(--muted);margin-top:6px}
.feat-icon{position:absolute;width:40px;height:40px}

/* what we do */
.wwd{left:0;top:1343px;width:1200px;height:412px;background:linear-gradient(90deg,#3a3937 0%,#4a4845 50%,#2f2e2c 100%)}
.wwd-title{left:163px;top:1403px;font-family:'Montserrat',sans-serif;font-weight:700;font-size:31px;color:var(--orange)}
.wwd-line{left:402px;top:1421px;width:75px;height:1px;background:#bbb}
.svc-list{left:163px;top:1470px;list-style:none;font-family:'Montserrat',sans-serif;font-size:12px;color:var(--white)}
.svc-list li{height:30px;line-height:16px}
.svc-list li.on{color:var(--orange)}
.wwd-text{left:395px;top:1470px;width:265px;font-size:10.5px;line-height:16.5px;color:#e8e8e8}
.wwd-text p+p{margin-top:14px}
.learn-btn{left:395px;top:1661px;width:110px;height:32px;line-height:32px;font-size:11px}
.wwd-img{left:724px;top:1470px;width:313px;height:224px;border:3px solid var(--white);background:linear-gradient(160deg,#e9e6e1,#cfc4b4 55%,#7b6b5a)}

/* stats */
.stats{left:0;top:2385px;width:1200px;height:307px;background:linear-gradient(90deg,#4a3f36 0%,#5d5d5e 45%,#777a7b 100%)}
.stats-head{left:0;top:2444px;width:1200px;text-align:center;font-family:'Montserrat',sans-serif;font-weight:700;font-size:30px;color:var(--white)}
.stats-rule{top:2464px;width:75px;height:1px;background:#ccc}
.stat{top:2521px;width:202px;height:110px;background:rgba(242,106,27,.85);text-align:center;color:var(--white);font-family:'Montserrat',sans-serif}
.stat b{display:block;font-size:34px;font-weight:700;margin-top:22px}
.stat span{display:block;font-size:11.5px;margin-top:4px;font-weight:500}

/* feedback */
.fb-card{left:423px;top:2829px;width:436px;height:172px;background:var(--white);box-shadow:0 0 8px rgba(0,0,0,.08)}
.fb-quote{left:464px;top:2820px;width:50px;height:48px;background:var(--orange);color:var(--white);font-family:'Montserrat',sans-serif;font-weight:700;font-size:56px;line-height:68px;text-align:center}
.fb-text{left:464px;top:2893px;width:370px;font-style:italic;font-size:11px;line-height:21px;color:var(--muted)}
.arrow{width:34px;height:34px;border-radius:50%;border:1px solid #ddd;background:var(--white)}
.fb-photo{left:338px;top:2982px;width:118px;height:119px;border:3px solid var(--ink);background:linear-gradient(180deg,#e9e9ea,#bcbcbf)}
.fb-name{left:490px;top:3036px;font-family:'Montserrat',sans-serif;font-size:15px;color:var(--orange)}
.fb-role{left:490px;top:3064px;font-family:'Montserrat',sans-serif;font-size:11px;color:var(--ink)}

/* contact */
.field{border:1px solid var(--line);background:var(--white);font-size:10px;color:#aaa;padding:14px 12px}
.send-btn{left:306px;top:3482px;width:175px;height:36px;line-height:36px;font-size:12px}
.ct-name{left:677px;top:3272px;font-family:'Montserrat',sans-serif;font-size:14px;color:var(--orange)}
.ct-row{left:677px;font-size:11px;color:var(--ink);font-family:'Montserrat',sans-serif}
.ct-row b{font-weight:600;display:inline-block;width:66px}
.ct-row span{color:#777;font-family:'Lato',sans-serif}
.skyline{left:0;top:3500px;width:1200px;height:175px;background:linear-gradient(180deg,rgba(255,255,255,0) 0%,#e3e3e3 60%,#cfcfcf 100%)}

/* footer */
.footer{left:0;top:3675px;width:1200px;height:290px;background:var(--footer)}
.foot-brand{left:204px;top:3740px;width:94px;text-align:center;font-family:'Montserrat',sans-serif;color:var(--white)}
.foot-brand .brand-mark{width:24px;height:24px}
.foot-brand .brand-name{font-size:14px}
.iso{left:150px;top:3832px;width:200px;text-align:center;font-family:'Montserrat',sans-serif;font-size:14px;color:var(--white)}
.social{top:3874px;width:32px;height:32px;background:var(--orange)}
.foot-h{top:3738px;font-family:'Montserrat',sans-serif;font-weight:700;font-size:13px;color:var(--orange)}
.foot-links{left:389px;top:3772px;list-style:none;font-size:10.5px;color:#ddd}
.foot-links li{height:23px}
.foot-text{font-size:10.5px;line-height:17px;color:#eee}
.news-input{left:838px;top:3834px;width:199px;height:36px;background:var(--white);font-size:10px;color:#aaa;padding:12px}
.sub-btn{left:838px;top:3881px;width:108px;height:33px;line-height:33px;font-size:11px}
.copy{left:0;top:3965px;width:1200px;height:73px;background:var(--footer-deep);text-align:center;line-height:73px;font-size:10px;color:#aaa}
</style>
</head>
<body>

<!-- hero -->
<div class="photo hero" role="img" aria-label="Timber-framed house under construction with brick walls against a cloudy sky"></div>
<svg class="abs hero-cut" width="1200" height="720" viewBox="0 0 1200 720">
  <polygon points="0,600 600,700 1200,560 1200,720 0,720" fill="#fff"/>
</svg>

<div class="abs brand"><div class="brand-mark"></div><div class="brand-name">SUMMIT<br>BUILDERS</div></div>

<nav class="abs nav">
  <a class="active" style="left:0">HOME</a>
  <a style="left:66px">ABOUT US</a>
  <a style="left:141px">SERVICES</a>
  <a style="left:212px">PROJECTS/PORTFOLIO</a>
  <a style="left:347px">CONTACT US</a>
</nav>
<svg class="abs search" width="18" height="18" viewBox="0 0 18 18"><circle cx="7.5" cy="7.5" r="5.5" fill="none" stroke="#333" stroke-width="1.8"/><line x1="11.5" y1="11.5" x2="16" y2="16" stroke="#333" stroke-width="1.8"/></svg>
<div class="abs btn quote-btn">REQUEST A QUOTE</div>

<h1 class="abs hero-title">THE BEST <span class="hl">CHOOSE</span><br><span class="hl">US BECAUSE</span> WE<br>DELIVER</h1>

<div class="abs badge">SUMMIT<br>BUILDERS</div>

<!-- who we are -->
<div class="abs rule" style="left:400px;top:789px;width:400px"></div>
<h2 class="abs sec-head" style="top:770px"><span>WHO WE ARE</span></h2>
<p class="abs who-sub">We Deliver Landmark Projects</p>
<p class="abs who-text">We are rethoric question ran over her cheek When she reached the first hills of the Italic Mountains, she had a last view back on the skyline of her hometown Bookmarksgrove, the headline of Alphabet Village and the subline of her own road, the Line Lane.</p>

<div class="abs feat-bg" style="left:392px;top:971px;width:415px;height:283px"></div>
<div class="photo" style="left:431px;top:945px;width:337px;height:337px;background:linear-gradient(160deg,#f08a3e,#d8652a 60%,#b24e22)" role="img" aria-label="Hands holding small wooden house models under an orange tint"></div>

<div class="abs feat" style="left:161px;top:997px;width:292px;height:100px">
  <h4>We've reputation for<br>excellence</h4><p>Lorem ipsum dolor sit amet, consectetur.</p>
</div>
<svg class="feat-icon" style="left:388px;top:1018px" viewBox="0 0 40 40"><circle cx="20" cy="16" r="11" fill="none" stroke="#f26a1b" stroke-width="1.6"/><path d="M13 25 L10 37 L16 33 L20 37 L20 27 M27 25 L30 37 L24 33 L20 37" fill="none" stroke="#333" stroke-width="1.4"/><polygon points="20,10 22,15 27,15 23,18 24,23 20,20 16,23 17,18 13,15 18,15" fill="none" stroke="#333" stroke-width="1.2"/></svg>

<div class="abs feat" style="left:161px;top:1128px;width:292px;height:105px">
  <h4>Guided by commitment</h4><p>Lorem ipsum dolor sit amet, consectetur adipiscing eiusmod tempor.</p>
</div>
<svg class="feat-icon" style="left:388px;top:1160px" viewBox="0 0 40 40"><rect x="4" y="18" width="8" height="18" fill="none" stroke="#f26a1b" stroke-width="1.6"/><path d="M12 20 L19 8 Q22 6 23 10 L21 18 L33 18 Q36 19 35 22 L32 34 Q31 36 28 36 L12 34" fill="none" stroke="#333" stroke-width="1.6"/></svg>

<div class="abs feat" style="left:746px;top:997px;width:291px;height:100px;padding-left:88px">
  <h4>We build partnerships</h4><p>Lorem ipsum dolor sit amet, consectetur adipiscing eiusmod tempor.</p>
</div>
<svg class="feat-icon" style="left:768px;top:1024px" viewBox="0 0 40 40"><rect x="9" y="4" width="20" height="16" fill="none" stroke="#333" stroke-width="1.4"/><circle cx="19" cy="12" r="4" fill="none" stroke="#f26a1b" stroke-width="1.4"/><path d="M2 30 L12 24 L20 28 L28 24 L38 30 M12 24 L18 34 M28 24 L22 34" fill="none" stroke="#333" stroke-width="1.4"/></svg>

<div class="abs feat" style="left:746px;top:1128px;width:291px;height:105px;padding-left:88px">
  <h4>A team of professionals</h4><p>Lorem ipsum dolor sit amet, consectetur adipiscing eiusmod tempor.</p>
</div>
<svg class="feat-icon" style="left:768px;top:1160px" viewBox="0 0 40 40"><circle cx="11" cy="14" r="5" fill="none" stroke="#f26a1b" stroke-width="1.5"/><circle cx="29" cy="14" r="5" fill="none" stroke="#f26a1b" stroke-width="1.5"/><circle cx="20" cy="18" r="5" fill="none" stroke="#333" stroke-width="1.5"/><path d="M2 32 Q11 20 18 28 M38 32 Q29 20 22 28 M10 38 Q20 24 30 38" fill="none" stroke="#333" stroke-width="1.5"/></svg>

<!-- what we do -->
<div class="photo wwd" role="img" aria-label="Construction crew at work on a site at dusk, darkened"></div>
<h2 class="abs wwd-title">WHAT WE DO</h2>
<div class="abs wwd-line"></div>
<ul class="abs svc-list">
  <li>HOME CONSTRUCTION</li><li>BUILDING REMODELING</li><li class="on">INTERIOR DESIGN</li><li>EXTERIOR DESIGN</li><li>RENOVATIONS</li><li>SAFETY MANAGEMENT</li>
</ul>
<div class="abs wwd-text">
  <p>Lorem ipsum dolor sit amet, consectetur adipiscing elit, sed do eiusmod tempor incididunt ut labore et dolore magna aliqua. Ut enim ad minim veniam, quis nostrud exercitation ullamco laboris nisi ut aliquip commodo consequat.</p>
  <p>Duis aute irure dolor in reprehenderit in voluptate velit esse cillum dolore eu fugiat nulla pariatur. Excepteur sint occaecat cupidatat non proident, sunt in culpa qui officia deserunt mollit anim id est laborum.</p>
</div>
<div class="abs btn learn-btn">LEARN MORE</div>
<div class="photo wwd-img" role="img" aria-label="Bright remodeled kitchen with white cabinets and island"></div>

<!-- projects -->
<div class="abs rule" style="left:380px;top:1832px;width:440px"></div>
<h2 class="abs sec-head" style="top:1813px"><span>OUR PROJECTS</span></h2>
<div class="photo" style="left:161px;top:2003px;width:195px;height:194px;background:linear-gradient(160deg,#c9a27a,#f2ede6 50%,#e0d6c8)" role="img" aria-label="Kitchen with wooden ceiling beams"></div>
<div class="photo" style="left:379px;top:1884px;width:268px;height:208px;background:linear-gradient(180deg,#e9eef2,#d9d3cc 50%,#9a8f86 85%,#7d8a6b)" role="img" aria-label="Modern apartment building"></div>
<div class="photo" style="left:671px;top:1943px;width:149px;height:149px;background:linear-gradient(180deg,#cfe0ee,#ece9e3 50%,#8aa36e)" role="img" aria-label="White two-storey house with palm trees"></div>
<div class="photo" style="left:845px;top:2018px;width:192px;height:195px;background:linear-gradient(180deg,#7fb0e0,#d8d4cc 55%,#6f9a4e)" role="img" aria-label="Contemporary villa with lawn"></div>
<div class="photo" style="left:379px;top:2115px;width:149px;height:149px;background:linear-gradient(180deg,#b8c3cf,#4f4f52 60%,#2f3335)" role="img" aria-label="Angular modern house at dusk"></div>
<div class="photo" style="left:552px;top:2115px;width:268px;height:209px;background:linear-gradient(160deg,#f1f1f1,#c9b79c 50%,#3f5373)" role="img" aria-label="Kitchen with navy cabinets and wood island"></div>

<!-- stats -->
<div class="photo stats" role="img" aria-label="Office interior under construction, darkened"></div>
<div class="abs stats-rule" style="left:405px"></div>
<div class="abs stats-rule" style="left:722px"></div>
<h2 class="abs stats-head">OUR STARTS</h2>
<div class="abs stat" style="left:161px"><b>53</b><span>TOTAL PROJECTS</span></div>
<div class="abs stat" style="left:387px"><b>371</b><span>STAFF MEMBERS</span></div>
<div class="abs stat" style="left:611px"><b>15</b><span>WORKING IN STATES</span></div>
<div class="abs stat" style="left:836px"><b>2,600</b><span>HOURS FOR WORK</span></div>

<!-- feedback -->
<div class="abs rule" style="left:340px;top:2762px;width:520px"></div>
<h2 class="abs sec-head" style="top:2743px"><span>CLIENT'S FEEDBACK</span></h2>
<div class="abs fb-card"></div>
<div class="abs fb-quote">&ldquo;</div>
<p class="abs fb-text">Summit Builders is one of the best general contractors we've worked with. The entire team tactfully delivered a project of exceptional quality while staying on schedule and under budget. We hope to work with Summit again in the near future!</p>
<svg class="abs arrow" style="left:350px;top:2898px" viewBox="0 0 34 34"><polyline points="19,11 13,17 19,23" fill="none" stroke="#333" stroke-width="1.6"/></svg>
<svg class="abs arrow" style="left:898px;top:2898px" viewBox="0 0 34 34"><polyline points="15,11 21,17 15,23" fill="none" stroke="#333" stroke-width="1.6"/></svg>
<div class="photo fb-photo" role="img" aria-label="Portrait of client"></div>
<div class="abs fb-name">Dana Whitley</div>
<div class="abs fb-role">Project Manager</div>

<!-- contact -->
<div class="abs rule" style="left:400px;top:3227px;width:400px"></div>
<h2 class="abs sec-head" style="top:3208px"><span>CONTACT US</span></h2>
<div class="abs field" style="left:161px;top:3272px;width:224px;height:42px">Name :</div>
<div class="abs field" style="left:401px;top:3272px;width:224px;height:42px">Phone :</div>
<div class="abs field" style="left:161px;top:3333px;width:464px;height:42px">Email :</div>
<div class="abs field" style="left:161px;top:3392px;width:464px;height:72px">Message / comments :</div>
<div class="abs btn send-btn">SEND MESSAGE</div>

<div class="abs ct-name">Marcus T Ellery | Branch Manager</div>
<div class="abs ct-row" style="top:3300px"><b>Address :</b><span style="display:inline-block;width:180px;vertical-align:top;line-height:17px">412 W Orchard Ave Riverside,<br>CA 92501</span></div>
<div class="abs ct-row" style="top:3359px"><b>Office :</b><span>555-210-4481</span></div>
<div class="abs ct-row" style="top:3385px"><b>Direct :</b><span>555-318-2207</span></div>
<div class="abs ct-row" style="top:3411px"><b>Fax :</b><span>555-210-4490</span></div>
<div class="abs ct-row" style="top:3452px"><b>Email :</b><span>mellery@summitbuildersca.example</span></div>

<div class="photo skyline" role="img" aria-label="Faint grey city skyline with construction cranes"></div>

<!-- footer -->
<footer class="abs footer"></footer>
<div class="abs foot-brand"><div class="brand-mark"></div><div class="brand-name">SUMMIT<br>BUILDERS</div></div>
<div class="abs iso">ISO 9001 : 2017</div>
<div class="abs social" style="left:177px" aria-label="Social link"></div>
<div class="abs social" style="left:215px" aria-label="Social link"></div>
<div class="abs social" style="left:253px" aria-label="Social link"></div>
<div class="abs social" style="left:291px" aria-label="Social link"></div>

<h3 class="abs foot-h" style="left:389px">LINKS</h3>
<ul class="abs foot-links">
  <li>- Home</li><li>- About Us</li><li>- Services</li><li>- Projects / Portfolio</li><li>- Contact</li>
</ul>

<h3 class="abs foot-h" style="left:613px">WORKING HOURS</h3>
<p class="abs foot-text" style="left:613px;top:3772px;width:180px">We work 7 days a week, every day excluding major holidays. Contact us if you have an emergency, with our Hotline and Contact form.</p>
<p class="abs foot-text" style="left:613px;top:3846px;width:200px;line-height:23px">Monday - Friday: 10:00 – 16:00<br>Saturday : 12:00 – 15:00<br>Sunday and holidays : 09:00 – 12:00</p>

<h3 class="abs foot-h" style="left:838px">STAY UPDATED</h3>
<p class="abs foot-text" style="left:838px;top:3772px;width:200px">Lorem ipsum dolor sit amet, consectetur adipiscing elit, sed do eiusmod tempor incididunt ut labore et dolore.</p>
<div class="abs news-input">Email Address :</div>
<div class="abs btn sub-btn">SUBCRIBE NOW</div>

<div class="abs copy">Copyright © 2020 Summit Builders - All Right Reserved.</div>

</body>
</html>
```